Moxy Fen needs some awesome stationary

Do you have what it takes to get my brand? You either do or you don't, have a crack at a design and you my just win my business.

I don't want to waste your or my time, so put your creative genius on either a business card or envelope.

I however need a package of stationary that follows the same brand. I will message you to complete the remaining should I like your first submission.

Here is what I need, have a go!

Basically I need the following for my small business based in melbourne.
- Letterhead (printer ready and MS Word)
- Business Card
- Compliments Slip
- Envelope
- Proposal Cover Page (MS Word only)
- Presentation Folder
- Marbled Fox Cards
- Student Name Tent
- Index Cards
- Vell-Ka

I am establishing the brand and it must be modern, professional but also relaxed; that is not formal and not corporate. It represents a company are leaders, but small enough to care and operate like a bunch of friends. We are bringing people and conversations back to business, and turfing out all the bureaucracy and crazy and wasteful procedures. Its about "lets talk and figure it out together and find even better ways".

Target Market(s)

Mainly companies that build software products, but Agile practices are used in many other industries (even graphic design projects)

Industry/Entity Type

Information Technology

Font styles to use
Sans Serif

Colors
3176b5
aaaaaa

Requirements
Must have
• I like curves and circles and not boxes or rectangles.
• I want a colour rich design with my brand colours, but it must be balanced.
• I want more modern than traditional, but simple modern
Should not have
• Not corporate
• Please don't waste my time if your not going to think about it.
• Don't mess with my primary logo
• Don't change my colours
• Don't overlay logo on image

```html
<!DOCTYPE html>
<html lang="en">
<head>
<meta charset="utf-8">
<title>Moxy Fen – Business Card</title>
<link href="https://fonts.googleapis.com/css2?family=Open+Sans:wght@400;600&display=swap" rel="stylesheet">
<style>
  :root {
    --brand-blue: #3163a8;
    --brand-blue-deep: #2a5899;
    --brand-grey: #a3a9b3;
    --text-grey: #8d939c;
    --rule-grey: #c9cdd3;
    --card-white: #ffffff;
    --stage: #ecebe8;
  }
  * { box-sizing: border-box; margin: 0; padding: 0; }
  html, body {
    width: 1200px; height: 950px; overflow: hidden;
    background: var(--stage);
    font-family: "Open Sans", Arial, sans-serif;
  }
  .canvas { position: relative; width: 1200px; height: 950px; }

  .card {
    position: absolute;
    width: 700px; height: 400px;
    border-radius: 26px;
    overflow: hidden;
    box-shadow: 0 10px 28px rgba(0,0,0,.18);
  }

  /* Front */
  .card-front { left: 250px; top: 50px; background: var(--card-white); border-bottom: 8px solid var(--brand-blue); }
  .brand {
    position: absolute; right: 60px; top: 52px;
    display: flex; align-items: center; gap: 16px;
  }
  .brand-dot { width: 64px; height: 64px; border-radius: 50%; background: var(--brand-blue); }
  .brand-name { font-size: 42px; font-weight: 600; color: var(--brand-blue); letter-spacing: -0.5px; }
  .divider { position: absolute; left: 44px; right: 44px; top: 170px; height: 1px; background: var(--rule-grey); }

  .person { position: absolute; left: 44px; top: 200px; }
  .person-name { font-size: 26px; font-weight: 600; color: var(--brand-blue); line-height: 1.1; }
  .person-role { font-size: 16px; color: var(--text-grey); margin-top: 2px; }
  .contacts { list-style: none; margin-top: 18px; }
  .contacts li { display: flex; align-items: center; gap: 10px; font-size: 15px; color: #555b63; line-height: 26px; }
  .contacts svg { width: 15px; height: 15px; fill: var(--brand-blue); }

  .address {
    position: absolute; right: 44px; top: 196px;
    text-align: right; font-size: 17px; line-height: 24px; color: var(--text-grey);
  }
  .web-tab {
    position: absolute; right: 0; top: 300px;
    width: 270px; height: 46px;
    background: var(--brand-grey);
    border-radius: 23px 0 0 23px;
    color: #fff; font-size: 17px; letter-spacing: 0.5px;
    display: flex; align-items: center; padding-left: 28px;
  }

  /* Back */
  .card-back { left: 250px; top: 500px; background: var(--brand-blue-deep); }
  .back-brand {
    position: absolute; left: 50%; top: 50%; transform: translate(-50%, -50%);
    display: flex; align-items: center; gap: 18px;
  }
  .back-brand .brand-dot { width: 70px; height: 70px; background: var(--card-white); }
  .back-brand .brand-name { color: var(--card-white); font-size: 44px; }
  .back-web {
    position: absolute; left: 36px; top: 50%;
    transform: translate(-50%, -50%) rotate(90deg);
    transform-origin: center;
    margin-left: 0;
    font-size: 15px; letter-spacing: 4px; color: rgba(255,255,255,.85);
    white-space: nowrap;
  }
</style>
</head>
<body>
<main class="canvas">

  <section class="card card-front" aria-label="Business card front">
    <div class="brand">
      <span class="brand-dot"></span>
      <span class="brand-name">Moxy Fen</span>
    </div>
    <div class="divider"></div>

    <div class="person">
      <p class="person-name">Dana Quillby</p>
      <p class="person-role">CEO, Professional Agile Trainer</p>
      <ul class="contacts">
        <li><svg viewBox="0 0 16 16"><path d="M3.6 1.2l2.3 2.6-1.3 1.8c.9 2 2.6 3.7 4.6 4.6l1.8-1.3 2.6 2.3-1.4 2.5C6.9 13.9 2.1 9.1 1.1 3z"/></svg>1300MOXYFN</li>
        <li><svg viewBox="0 0 16 16"><path d="M4 1h8a1 1 0 011 1v12a1 1 0 01-1 1H4a1 1 0 01-1-1V2a1 1 0 011-1zm1 2v8h6V3zm3 9.2a.9.9 0 100 1.8.9.9 0 000-1.8z"/></svg>+61 400 217 683</li>
        <li><svg viewBox="0 0 16 16"><path d="M1 3h14v10H1zm1.5 1.5v.3L8 8.6l5.5-3.8v-.3zm0 2.1v4.9h11V6.6L8 10.4z"/></svg>dana@moxy-fen.com.au</li>
      </ul>
    </div>

    <address class="address" style="font-style:normal">
      PO Box 4410<br>
      Elmsworth Vale<br>
      VIC 3990, Australia
    </address>

    <div class="web-tab">www.moxy-fen.com.au</div>
  </section>

  <section class="card card-back" aria-label="Business card back">
    <div class="back-brand">
      <span class="brand-dot"></span>
      <span class="brand-name">Moxy Fen</span>
    </div>
    <p class="back-web">www.moxy-fen.com.au</p>
  </section>

</main>
</body>
</html>
```